Business Card Design for a Personal Trainer

I need a business card design for my job as a personal trainer. It should have a unique, modern and exclusive design. On the front there should be only my logo with my name and my job. 0162/3819204 Tobias Lendhart Wiesengrundweg 14 80417 Munich Germany The most important contact information is the web adress. it can be bigger than the rest, but its not necessary. The card should be 8,5cmx5,5cm big. Font: Roboto. Colors: black, white, gray, 56c1ff.

```html
<!DOCTYPE html>
<html lang="de">
<head>
<meta charset="utf-8">
<title>Tobias Lendhart – Personal Trainer Business Card</title>
<link rel="stylesheet" href="https://fonts.googleapis.com/css2?family=Roboto:wght@300;400;500&display=swap">
<style>
  :root {
    --bg: #e4e4e2;
    --black: #1f1d1e;
    --white: #ffffff;
    --paper: #f3f3f3;
    --gray: #4a4a4a;
    --sky: #56c1ff;
  }
  * { box-sizing: border-box; margin: 0; padding: 0; }
  html, body {
    width: 1200px; height: 900px; overflow: hidden;
    background: var(--bg);
    font-family: "Roboto", Arial, sans-serif;
  }
  .stage {
    position: relative; width: 1200px; height: 900px;
    display: flex; align-items: center; justify-content: center; gap: 40px;
  }
  .card {
    position: relative; width: 520px; height: 336px; overflow: hidden;
    box-shadow: 0 6px 18px rgba(0,0,0,0.18);
  }
  /* Front */
  .card--front { background: var(--black); display: flex; align-items: center; justify-content: center; }
  .brand { text-align: center; color: var(--white); }
  .brand__name {
    font-size: 30px; font-weight: 400; letter-spacing: 1px; text-transform: uppercase;
  }
  .brand__role {
    display: flex; align-items: center; gap: 8px; margin-top: 4px;
    font-size: 11px; font-weight: 400; letter-spacing: 4.5px; text-transform: uppercase;
  }
  .brand__role::before, .brand__role::after {
    content: ""; flex: 1; height: 1px; background: currentColor;
  }
  /* Back */
  .card--back { background: var(--paper); }
  .card__photo {
    position: absolute; left: 330px; top: 14px; width: 190px; height: 200px;
    background: radial-gradient(ellipse at 55% 60%, #6a6a6a 0%, #9a9a9a 50%, rgba(243,243,243,0) 78%);
  }
  .card__waves { position: absolute; inset: 0; }
  .card__back-brand { position: absolute; left: 46px; top: 78px; color: var(--black); }
  .card__back-brand .brand__name { font-size: 26px; }
  .card__back-brand .brand__role { font-size: 10px; letter-spacing: 4px; }
  .contact {
    position: absolute; left: 46px; top: 150px; color: var(--black);
    font-size: 15px; line-height: 20px;
  }
  .contact__line { display: flex; align-items: center; gap: 6px; font-weight: 500; }
  .contact__icon { width: 13px; height: 13px; fill: var(--sky); flex: none; }
  .contact__address { margin-top: 8px; color: var(--gray); font-weight: 400; }
  .website {
    position: absolute; right: 26px; top: 238px; color: var(--white);
    font-size: 17px; font-weight: 400;
  }
</style>
</head>
<body>
<main class="stage">
  <section class="card card--front">
    <div class="brand">
      <div class="brand__name">Tobias Lendhart</div>
      <div class="brand__role">Personal Trainer</div>
    </div>
  </section>

  <section class="card card--back">
    <div class="card__photo" role="img" aria-label="Black and white portrait photo of the trainer in a sports shirt"></div>
    <svg class="card__waves" viewBox="0 0 520 336" aria-hidden="true">
      <path fill="var(--sky)" d="M0,268 C140,286 250,238 382,188 C300,234 160,306 0,300 Z"/>
      <path fill="var(--black)" d="M0,300 C140,310 260,250 360,205 C420,180 480,168 520,164 L520,336 L0,336 Z"/>
    </svg>
    <div class="card__back-brand">
      <div class="brand__name">Tobias Lendhart</div>
      <div class="brand__role">Personal Trainer</div>
    </div>
    <div class="contact">
      <div class="contact__line">
        <svg class="contact__icon" viewBox="0 0 16 16"><path d="M3 1l3 0 1 4-2 1.5c1 2 2.5 3.5 4.5 4.5L11 9l4 1v3c0 1-1 2-2 2C7 15 1 9 1 3c0-1 1-2 2-2z"/></svg>
        <span>0162/3819204</span>
      </div>
      <div class="contact__line">
        <svg class="contact__icon" viewBox="0 0 16 16"><path d="M1 3h14v10H1z M1 3l7 6 7-6" stroke="var(--paper)" stroke-width="1"/></svg>
        <span>t.lendhart@postfeld.de</span>
      </div>
      <div class="contact__address">Wiesengrundweg 14<br>80417 München</div>
    </div>
    <div class="website">www.tobiaslendhart.de</div>
  </section>
</main>
</body>
</html>
```